The most modern business card ever !!!

Our company call “Vendalo”. Vendalo is a technology company specialized in cruises solutions. Out main product is a platform to reserve cruises. This is a revolutionary platform that make easier to travel agencies and final users to reserve cruises across dozen companies like tibba, wernu, hpv, dgb, etc..We are a “start up”, with a young team of developers and we want to transmit it.. For it, we want something different, a modern business card that represent cruises and technology.. When someone receive this card, this person should say: wowww this is different… this is modern… this is a cruise related company..
- diferent, modern
- traditions business card

```html
<!DOCTYPE html>
<html lang="en">
<head>
<meta charset="utf-8">
<title>Vendalo business card</title>
<link rel="stylesheet" href="https://fonts.googleapis.com/css2?family=Work+Sans:wght@400;500;600&display=swap">
<style>
  :root {
    --canvas: #2b2b2d;
    --card-light: #ffffff;
    --card-light-shade: #eeeeef;
    --card-dark: #141414;
    --ink: #1a1a1a;
    --ink-soft: #2c2c2c;
    --accent: #2a9fd8;
    --mark-light: #c9c9c9;
  }
  * { margin: 0; padding: 0; box-sizing: border-box; }
  html, body {
    width: 1200px;
    height: 900px;
    overflow: hidden;
    background: var(--canvas);
    font-family: "Work Sans", Arial, sans-serif;
  }
  .canvas {
    width: 1200px;
    height: 900px;
    display: flex;
    flex-direction: column;
    align-items: center;
    justify-content: center;
    gap: 48px;
  }
  .card {
    position: relative;
    width: 660px;
    height: 378px;
    border-radius: 3px;
    box-shadow: 0 14px 34px rgba(0, 0, 0, 0.45);
    overflow: hidden;
  }
  .card--front {
    background: radial-gradient(ellipse at 55% 70%, var(--card-light) 45%, var(--card-light-shade) 100%);
  }
  .card--back {
    background: var(--card-dark);
    display: flex;
    align-items: center;
    justify-content: center;
  }

  .person {
    position: absolute;
    left: 44px;
    top: 44px;
  }
  .person__name {
    font-size: 22px;
    font-weight: 500;
    letter-spacing: 0.5px;
    color: var(--accent);
    text-transform: uppercase;
  }
  .person__role {
    font-size: 14px;
    font-weight: 400;
    color: var(--ink-soft);
    margin-top: 2px;
    letter-spacing: 0.5px;
  }
  .divider {
    position: absolute;
    left: 128px;
    right: 60px;
    top: 96px;
    height: 1px;
    background: var(--accent);
  }

  .contact {
    position: absolute;
    left: 44px;
    top: 124px;
    list-style: none;
    font-size: 14px;
    line-height: 26px;
    color: var(--ink);
    letter-spacing: 0.4px;
  }
  .contact__item {
    display: flex;
    align-items: center;
    gap: 8px;
  }
  .contact__address { padding-left: 20px; line-height: 22px; margin-bottom: 6px; }
  .contact__icon { width: 12px; height: 12px; flex: none; }
  .contact__highlight { color: var(--accent); }

  .brand {
    display: flex;
    align-items: center;
    gap: 10px;
    font-weight: 600;
    letter-spacing: 1px;
  }
  .brand__square {
    display: block;
    background: var(--accent);
  }
  .card--front .brand {
    position: absolute;
    right: 56px;
    top: 150px;
    font-size: 52px;
    color: var(--ink);
  }
  .card--front .brand__square { width: 18px; height: 18px; }
  .card--back .brand {
    font-size: 78px;
    color: var(--mark-light);
  }
  .card--back .brand__square { width: 24px; height: 24px; }
</style>
</head>
<body>
<main class="canvas">
  <section class="card card--front" aria-label="Business card front">
    <div class="person">
      <p class="person__name">Daniel Ostrander</p>
      <p class="person__role">Director</p>
    </div>
    <div class="divider"></div>
    <ul class="contact">
      <li class="contact__address">48b Harlow Lane,<br>Westbury, NZ, 4410</li>
      <li class="contact__item">
        <svg class="contact__icon" viewBox="0 0 12 12" aria-hidden="true"><path d="M3 1 L5 3.5 L4 5 Q5 7 7 8 L8.5 7 L11 9 L9.5 11 Q5 11 2.5 8 Q1 5.5 1 3 Z" fill="var(--accent)"/></svg>
        <span>(555) 014-2290</span>
      </li>
      <li class="contact__item">
        <svg class="contact__icon" viewBox="0 0 12 12" aria-hidden="true"><rect x="1" y="2.5" width="10" height="7" fill="none" stroke="var(--accent)" stroke-width="1.2"/><path d="M1 2.5 L6 6.5 L11 2.5" fill="none" stroke="var(--accent)" stroke-width="1.2"/></svg>
        <span>info@vendalo.com.br</span>
      </li>
      <li class="contact__item">
        <svg class="contact__icon" viewBox="0 0 12 12" aria-hidden="true"><circle cx="6" cy="6" r="5" fill="none" stroke="var(--accent)" stroke-width="1.2"/><ellipse cx="6" cy="6" rx="2.2" ry="5" fill="none" stroke="var(--accent)" stroke-width="1"/><path d="M1 6 H11" stroke="var(--accent)" stroke-width="1"/></svg>
        <span>www.<span class="contact__highlight">vendalo</span>.com.br</span>
      </li>
    </ul>
    <div class="brand">
      <span class="brand__square"></span>
      <span class="brand__name">Vendalo</span>
    </div>
  </section>

  <section class="card card--back" aria-label="Business card back">
    <div class="brand">
      <span class="brand__square"></span>
      <span class="brand__name">Vendalo</span>
    </div>
  </section>
</main>
</body>
</html>
```